Kestrel Finish Studio (KFS)

I would like to design a dedicated site for my KFS product, which allows industry employees to be trained in the visual inspection of mechanical parts. My product is a 3D simulator (see https://morvint-works.ch/our-applications/virtual-reality/ and https://morvint-works.ch for videos) which makes it possible to manufacture standard parts representative of a type of defect which is accepted or refused by the quality department. These master parts can be used to create a common quality culture in the company and to train employees in a homogeneous way. The simulator is initially designed for watchmaking, but must be designed for much broader industries (cars, phone reconditioning, ball bearings, etc.)
L'information que j'ai donnée n'est pas assez précise. Je dois préciser les domaines métiers visés par le site internet. J'ai besoin de quelques jours pour choisir les domaines les plus représentatifs.
Coded - Design and coding required
1 page

```html
<!DOCTYPE html>
<html lang="en">
<head>
<meta charset="utf-8">
<title>Kestrel Finish Studio</title>
<link href="https://fonts.googleapis.com/css2?family=Unbounded:wght@700;800;900&family=Manrope:wght@400;500;600;700&display=swap" rel="stylesheet">
<style>
:root{
  --bg:#0a0d10;
  --panel-top:#0f1317;
  --panel-bottom:#2a3337;
  --blue:#1f7cff;
  --blue-deep:#0b5fe0;
  --text:#ffffff;
  --muted:#c4c9cf;
  --dim:#8a9097;
  --body:#e3e6ea;
}
*{margin:0;padding:0;box-sizing:border-box}
html,body{width:1200px;height:4396px;overflow:hidden;background:var(--bg)}
body{position:relative;font-family:"Manrope",sans-serif;color:var(--text);
  background:radial-gradient(circle at 1px 1px,#151a1f 1px,transparent 1.5px) 0 0/6px 6px,var(--bg)}
.abs{position:absolute}
.display{font-family:"Unbounded",sans-serif;font-weight:800;letter-spacing:.01em}
.btn{position:absolute;display:flex;align-items:center;justify-content:center;border-radius:4px;
  background:linear-gradient(180deg,#3a95ff,var(--blue-deep));color:#fff;font-size:16px;font-weight:600}
.photo{position:absolute}
/* wordmark: body font, one colour, one weight */
.wordmark{font-family:"Manrope",sans-serif;font-weight:700;color:var(--blue);letter-spacing:0}
.brand{left:92px;top:40px;font-size:21px}
.nav-link{top:45px;font-size:16px;color:var(--muted)}
.signup{left:997px;top:29px;width:113px;height:50px;border:2px solid var(--blue);border-radius:5px;
  display:flex;align-items:center;justify-content:center;font-weight:600;font-size:16px}
.hero-title{left:89px;top:172px;font-size:55px;line-height:72px;font-weight:900}
.hero-sub{left:92px;top:403px;font-size:17px;line-height:30px;letter-spacing:.02em;color:#e7eaee}
.learn{left:280px;top:503px;display:flex;align-items:center;gap:14px;color:var(--dim);font-size:16px}
.play{width:50px;height:50px;border-radius:50%;background:#2a2f35;display:flex;align-items:center;justify-content:center}
.section-title{left:0;width:1200px;text-align:center;font-size:24px;line-height:46px}
.panel{left:87px;top:772px;width:1024px;height:437px;border-radius:8px;
  background:linear-gradient(180deg,var(--panel-top),var(--panel-bottom));border:1px solid #1b2227}
.tick-item{display:flex;gap:30px;font-size:14.5px;line-height:18px;color:var(--body);width:430px}
.tick-item svg{flex:none;margin-top:2px}
.feature-title{font-size:24px;line-height:38px}
.feature-text{font-size:14.5px;line-height:22px;color:var(--body)}
.feature-text p+p{margin-top:22px}
.allow-item{display:flex;gap:22px;align-items:flex-start;left:88px;width:560px;font-size:12.5px;line-height:20px;color:var(--body)}
.allow-item svg{flex:none}
.testimonial{left:606px;top:3558px;width:505px;height:242px;border-radius:12px;
  background:linear-gradient(180deg,#0e1216,#2a3337);border:1px solid #1b2227}
.arrow{width:28px;height:28px;border-radius:50%;background:#1f2a36;display:flex;align-items:center;justify-content:center}
.cta{left:87px;top:3837px;width:1024px;height:290px;border-radius:20px;
  background:linear-gradient(180deg,#9ccbff 0%,#4f9dff 45%,#1c78ff 100%);text-align:center;color:#0c1220}
.foot-link{top:4188px;font-size:16px;color:var(--blue)}
.social{width:26px;height:26px;border-radius:50%;background:var(--blue);top:4300px}
</style>
</head>
<body>

<!-- navigation -->
<div class="abs wordmark brand">Kestrel Finish</div>
<div class="abs nav-link" style="left:372px">About Us</div>
<div class="abs nav-link" style="left:519px">Our Project</div>
<div class="abs nav-link" style="left:679px">Community</div>
<div class="abs nav-link" style="left:845px">Resources</div>
<div class="abs signup">Sign Up</div>

<!-- hero -->
<h1 class="abs display hero-title">Kestrel<br>Finish<br>Studio</h1>
<p class="abs hero-sub">VIRTUAL REALITY AT THE SERVICE OF CONTROLLED<br>AESTHETIC WATCHMAKING</p>
<div class="btn" style="left:89px;top:502px;width:152px;height:48px">Explore Now</div>
<div class="abs learn"><span class="play"><svg width="18" height="20" viewBox="0 0 18 20"><path d="M2 1l15 9-15 9z" fill="#1f7cff"/></svg></span>Learn More ›</div>
<div class="photo" role="img" aria-label="Woman wearing a VR headset reaching toward glowing particles"
  style="left:594px;top:177px;width:555px;height:383px;border-radius:0 0 0 30px;clip-path:polygon(12% 0,100% 0,100% 100%,0 100%,0 70%);
  background:radial-gradient(circle at 25% 35%,#3a6a8a 0%,transparent 35%),linear-gradient(135deg,#1a1f6a,#6a2a9a 45%,#1b3fa8 80%,#0c1430)"></div>

<!-- aesthetic control -->
<h2 class="abs display section-title" style="top:646px">Aesthetic Control: HOW TO<br>CONTROL IT?</h2>
<div class="abs panel"></div>
<svg width="0" height="0" style="position:absolute"><defs><symbol id="tick" viewBox="0 0 28 28"><circle cx="14" cy="14" r="11" fill="none" stroke="#1f7cff" stroke-width="2"/><path d="M8 14l5 5 13-14" fill="none" stroke="#1f7cff" stroke-width="3"/></symbol></defs></svg>
<div class="abs tick-item" style="left:120px;top:807px"><svg width="28" height="28"><use href="#tick"/></svg><span>Adopting a simple and unambiguous language for a common understanding of aesthetic quality at the extended enterprise level.</span></div>
<div class="abs tick-item" style="left:622px;top:807px"><svg width="28" height="28"><use href="#tick"/></svg><span>Providing uniform training in operational competence for those responsible for aesthetic control.</span></div>
<div class="abs tick-item" style="left:120px;top:944px"><svg width="28" height="28"><use href="#tick"/></svg><span>By using a semantic reference matrix associating the types of anomalies (scratches, marks, deformations, stains, etc.) with the intensity levels defined with the company.</span></div>
<div class="abs tick-item" style="left:622px;top:944px"><svg width="28" height="28"><use href="#tick"/></svg><span>By designing realistic and attractive teaching sequences for total quality control.</span></div>
<div class="abs tick-item" style="left:120px;top:1094px"><svg width="28" height="28"><use href="#tick"/></svg><span>Determining the compliance thresholds of the component or product.</span></div>
<div class="abs tick-item" style="left:622px;top:1094px"><svg width="28" height="28"><use href="#tick"/></svg><span>By regularly assessing the competence to measure the aesthetics, expressed in a tangible, reliable and sustainable way (R&amp;R), of a component or product.</span></div>

<!-- lighten management -->
<div class="abs" style="left:0;top:1465px;width:531px;height:426px;background:linear-gradient(135deg,#1a7cff,#0a4fd0);clip-path:polygon(0 0,78% 0,100% 92%,96% 100%,0 100%)"></div>
<div class="photo" role="img" aria-label="Young man in a blue t-shirt wearing a VR headset, raising his hands"
  style="left:80px;top:1240px;width:380px;height:651px;border-radius:60px 60px 0 0;background:linear-gradient(180deg,#24292f 0%,#2b6fd0 40%,#1e5fc0 100%);opacity:.85"></div>
<h3 class="abs display feature-title" style="left:673px;top:1354px">Lighten the<br>management of<br>physical components</h3>
<div class="abs feature-text" style="left:673px;top:1486px;width:460px">
  <p>Companies must manage and maintain sets of physical components used as a "yardstick" for the training of aesthetic testers.</p>
  <p>The cost of managing a set of physical parts representing all combinations of shapes, defect types, materials and finishes is very high.</p>
  <p>KFS allows the company to significantly reduce its management burden by scanning components or products in 3D and then virtually</p>
</div>
<div class="btn" style="left:673px;top:1736px;width:153px;height:44px">Learn More</div>

<!-- KFS allows -->
<h3 class="abs display" style="left:89px;top:1934px;font-size:24px">KFS allows :</h3>
<div class="abs allow-item" style="top:2004px"><svg width="40" height="40" viewBox="0 0 40 40" fill="none" stroke="#1f7cff" stroke-width="2"><circle cx="16" cy="16" r="8"/><circle cx="16" cy="16" r="3"/><circle cx="29" cy="28" r="6"/><path d="M16 4v4M16 24v4M4 16h4M24 16h4"/></svg><span>Remove the management of components used as standards for<br>aesthetic control training</span></div>
<div class="abs allow-item" style="top:2073px"><svg width="40" height="40" viewBox="0 0 40 40" fill="none" stroke="#1f7cff" stroke-width="2"><circle cx="20" cy="12" r="6"/><path d="M8 36c0-8 5-14 12-14s12 6 12 14"/></svg><span>To make employees aware of aesthetic control and the<br>vocabulary to be used</span></div>
<div class="abs allow-item" style="top:2145px"><svg width="40" height="40" viewBox="0 0 40 40" fill="none" stroke="#1f7cff" stroke-width="2"><path d="M20 4l13 5v10c0 9-6 15-13 18C13 34 7 28 7 19V9z"/><path d="M14 20l5 5 8-9"/></svg><span>Integrate aesthetic control into a total quality management<br>(TQM) approach with precise indicators at all stages of the<br>manufacturing and after-sales processes</span></div>
<div class="abs allow-item" style="top:2240px"><svg width="40" height="40" viewBox="0 0 40 40" fill="none" stroke="#1f7cff" stroke-width="2"><circle cx="20" cy="20" r="11"/><circle cx="20" cy="20" r="4"/><path d="M20 4v5M20 31v5M4 20h5M31 20h5M9 9l3 3M28 28l3 3M9 31l3-3M28 12l3-3"/></svg><span>Provide the after-sales service with an efficient tool to record the aesthetic<br>aspect of the supported product</span></div>
<div class="photo" role="img" aria-label="Woman wearing a white VR headset in a dim blue room"
  style="left:655px;top:1920px;width:545px;height:427px;clip-path:polygon(12% 0,100% 0,100% 100%,0 100%,0 94%);border-radius:0 0 0 24px;
  background:linear-gradient(135deg,#1d3a66,#4a4e5c 45%,#8a5a4a 75%,#2a2420)"></div>

<!-- raising awareness -->
<div class="photo" role="img" aria-label="Two people in white seated side by side wearing VR headsets in a bright cabin"
  style="left:0;top:2386px;width:531px;height:424px;clip-path:polygon(0 0,84% 0,90% 8%,100% 92%,95% 100%,0 100%);
  background:linear-gradient(180deg,#5fa8c4,#b8e4f0 40%,#6fb0cc 75%,#1f3a4a)"></div>
<h3 class="abs display feature-title" style="left:673px;top:2372px">Raising awareness of<br>criteria and aesthetic<br>vocabulary</h3>
<div class="abs feature-text" style="left:673px;top:2505px;width:460px">
  <p>Aesthetic defects are often the result of careless handling of the components and products concerned, whether during manufacture, assembly or marketing.</p>
  <p>By making the KFS platform available to staff in direct contact with the product, it becomes very easy to<br>make them aware of the evaluation criteria and the aesthetic vocabulary defined by the company. adding 'typical' aesthetic anomalies.</p>
</div>
<div class="btn" style="left:673px;top:2753px;width:153px;height:45px">Learn More</div>

<!-- after sales -->
<h3 class="abs display" style="left:89px;top:2856px;font-size:24px;line-height:30px">Improve after sales<br>service returns</h3>
<div class="abs feature-text" style="left:89px;top:2932px;width:400px;font-size:12.5px;line-height:20px">
  <p>The KFS platform can easily be used by the service network staff to assist them in the objective assessment of aesthetic defects by referring to the semantic matrix as well as to the cases already referenced.</p>
  <p style="margin-top:20px">It is also possible, in an intuitive and playful way, to indicate, in accordance with the product nomenclature, a type of imperfection, its intensity and its location. It is also possible to draw up a precise repair estimate or to declare a non-conformity on a product coming from a market return.</p>
</div>
<div class="photo" role="img" aria-label="Laughing woman in a plaid shirt wearing a VR headset in a warm room"
  style="left:657px;top:2840px;width:543px;height:427px;clip-path:polygon(12% 0,100% 0,100% 100%,0 100%,0 94%);
  background:linear-gradient(135deg,#2a2622,#6a5040 45%,#3a2c28 75%,#1a1614)"></div>

<!-- semantic matrix -->
<div class="photo" role="img" aria-label="Man in a VR headset under pink and blue light, hand raised"
  style="left:87px;top:3378px;width:439px;height:427px;border-radius:22px;background:linear-gradient(135deg,#7a3ad0,#c03a9a 50%,#3a4ad0)"></div>
<h3 class="abs display" style="left:609px;top:3400px;font-size:22px;line-height:30px">A semantic matrix of<br>aesthetic defects</h3>
<p class="abs" style="left:609px;top:3469px;width:400px;font-size:12px;line-height:19px;color:var(--body)">KFS is based on a semantic matrix that defines 5 levels of intensity for each of the 5 types of aesthetic defects referenced: Scratches · Marks · Deformations · Stains · Uniformity.</p>
<div class="abs testimonial">
  <h4 class="abs display" style="left:0;width:505px;text-align:center;top:24px;font-size:24px">Testimonial</h4>
  <p class="abs" style="left:37px;top:78px;width:430px;font-size:11.5px;line-height:19px;color:var(--body)">Lorem ipsum dolor sit amet, consectetur adipiscing elit, sed do eiusmod tempor incididunt ut labore et dolore magna aliqua. Quis ipsum suspendisse ultrices gravida. Risus commodo viverra maecenas accumsan lacus vel</p>
  <div class="abs display" style="left:37px;top:172px;font-size:11px;color:var(--blue)">Marlo Quince</div>
  <div class="abs" style="left:37px;top:191px;font-size:11px;color:var(--body)">School Principal</div>
  <div class="abs arrow" style="left:408px;top:178px"><svg width="10" height="10" viewBox="0 0 10 10"><path d="M7 1L3 5l4 4" stroke="#1f7cff" stroke-width="1.6" fill="none"/></svg></div>
  <div class="abs arrow" style="left:442px;top:178px"><svg width="10" height="10" viewBox="0 0 10 10"><path d="M3 1l4 4-4 4" stroke="#1f7cff" stroke-width="1.6" fill="none"/></svg></div>
</div>

<!-- call to action -->
<div class="abs cta">
  <h2 class="display" style="margin-top:50px;font-size:30px">Get Started with Kestrel Finish</h2>
  <p style="margin-top:24px;font-size:12.5px;line-height:18px;color:#1a2540">Lorem ipsum dolor sit amet, consectetur adipiscing elit, sed do eius-<br>mod tempor incididunt ut labore et dolore magna aliqua. Quis ipsum</p>
  <div class="abs" style="left:439px;top:195px;width:140px;height:44px;border-radius:5px;background:#0f1a2a;color:#fff;font-size:16px;font-weight:600;display:flex;align-items:center;justify-content:center">Get Started</div>
</div>

<!-- footer -->
<div class="abs wordmark" style="left:50px;top:4183px;font-size:25px">Kestrel Finish</div>
<div class="abs foot-link" style="left:724px">About</div>
<div class="abs foot-link" style="left:824px">Company</div>
<div class="abs foot-link" style="left:949px">Support</div>
<div class="abs foot-link" style="left:1065px">Movement</div>
<div class="abs" style="left:50px;top:4237px;width:1102px;height:1px;background:#6a7580"></div>
<div class="abs" style="left:50px;top:4273px;display:flex;align-items:center;gap:18px;font-size:12px;color:var(--body)">
  <svg width="20" height="20" viewBox="0 0 20 20"><circle cx="10" cy="10" r="10" fill="#ffffff"/><path d="M6 5c1 0 2 2 2 3l-1 1c1 2 2 3 4 4l1-1c1 0 3 1 3 2 0 1-1 2-2 2-4 0-9-5-9-9 0-1 1-2 2-2z" fill="#0a0d10"/></svg>
  <span>+41 00 555 01 20 / +41 00 555 01 21</span></div>
<div class="abs" style="left:50px;top:4302px;display:flex;align-items:center;gap:18px;font-size:12px;color:var(--body)">
  <svg width="20" height="20" viewBox="0 0 20 20" fill="none" stroke="#ffffff" stroke-width="1.4"><circle cx="10" cy="10" r="8.5"/><ellipse cx="10" cy="10" rx="4" ry="8.5"/><path d="M1.5 10h17M3 6h14M3 14h14"/></svg>
  <span>team@morvint-works.ch hello@kestrelfinish.ch</span></div>
<div class="abs" style="left:963px;top:4267px;font-size:10.5px;color:var(--body)">Terms &amp; Conditions</div>
<div class="abs" style="left:1079px;top:4267px;font-size:10.5px;color:var(--body)">Privacy Policy</div>
<div class="abs social" style="left:997px"></div>
<div class="abs social" style="left:1037px"></div>
<div class="abs social" style="left:1076px"></div>
<div class="abs social" style="left:1117px"></div>
<div class="abs" style="left:0;width:1200px;top:4352px;text-align:center;font-size:10px;color:var(--muted)">© 2023 Kestrel Finish. All Rights Reserved</div>

</body>
</html>
```